larkforge website

commerce website to sell cookeries, brackets, mailboxes and to show off homes built. Modern Steel in design see marlo cycles web page to be like: https://www.marlocycles-demo.com/en/ sorry its bright nest hosting word press divi

must be able to add products to page

Target Market(s)

mainly western states of U.S.

Industry/Entity Type

Building Product

Coding

Coded - Design and coding required

Number of Pages Required

3 page

Font styles to use
Sans Serif

Colors

Designer to choose colors to be used in the design.

Requirements
Must have
• customers to be able to order products from page
• bright nest hosting word press divi

```html
<!DOCTYPE html>
<html lang="en">
<head>
<meta charset="utf-8">
<title>Lark Forge — Modern Steel Products</title>
<link href="https://fonts.googleapis.com/css2?family=Ubuntu:wght@400;500&family=Mulish:wght@400;600;700&display=swap" rel="stylesheet">
<style>
:root{
  --brand:#4b5b84;
  --brand-dark:#3e4b6e;
  --ink:#111;
  --text:#777;
  --muted:#9a9a9a;
  --pale:#eef0f4;
  --white:#fff;
}
*{box-sizing:border-box;margin:0;padding:0}
html,body{width:1200px;height:3712px;overflow:hidden;background:var(--white)}
body{position:relative;font-family:"Mulish",sans-serif;color:var(--text)}
.abs{position:absolute}
.h-title{font-family:"Ubuntu",sans-serif;font-weight:400;color:var(--ink)}
.eyebrow{font-family:"Mulish",sans-serif;font-weight:700;font-size:13px;letter-spacing:3px;color:var(--brand)}
.copy{font-size:11.5px;line-height:19.5px;color:var(--text)}
.btn{position:absolute;display:flex;align-items:center;justify-content:center;background:var(--brand);color:var(--white);border-radius:4px;font-family:"Ubuntu",sans-serif;font-size:15px}
.hex{position:absolute;clip-path:polygon(25% 3%,75% 3%,100% 50%,75% 97%,25% 97%,0 50%)}
.hex-soft{position:absolute;background:var(--pale);clip-path:polygon(25% 3%,75% 3%,100% 50%,75% 97%,25% 97%,0 50%)}
.dots{position:absolute;background-image:radial-gradient(var(--muted) 1.2px,transparent 1.5px);background-size:15px 15px;opacity:.6}

/* header */
.brand-mark{left:160px;top:78px;color:var(--white);font-family:"Mulish",sans-serif;font-weight:700;font-size:21px;letter-spacing:1px}
.brand-dot{left:218px;top:30px;width:22px;height:22px;border-radius:50%;border:2px solid var(--white)}
.nav{left:345px;top:53px;display:flex;gap:33px;font-size:12px;color:#222}
.signup{left:833px;top:40px;width:90px;height:39px;background:var(--white);border-radius:4px;color:var(--brand);font-size:13px;font-weight:700;display:flex;align-items:center;justify-content:center}
.icon-hex{width:46px;height:50px}

/* hero */
.hero-title{left:162px;top:298px;font-size:55px;line-height:62px}
.hero-copy{left:162px;top:437px;width:460px;font-size:12px;line-height:20px}

/* products */
.photo-band{left:0;top:1555px;width:1038px;height:412px;background:linear-gradient(100deg,#2b2f3a,#4a5466 45%,#1f2430)}
.panel{position:absolute;background:var(--brand)}
.card{position:absolute;background:var(--white);box-shadow:0 4px 16px rgba(0,0,0,.12);text-align:center;font-size:14px;color:#333}
.product-photo{position:absolute;border-radius:4px}
.vlabel{position:absolute;writing-mode:vertical-rl;transform:rotate(180deg);color:var(--white);font-family:"Ubuntu",sans-serif;font-size:15px;letter-spacing:.5px}
.ghost{position:absolute;border:1px solid var(--white);border-radius:4px;color:var(--white);font-size:13px;display:flex;align-items:center;justify-content:center}

/* testimonials */
.quote-card{left:330px;top:2833px;width:540px;height:204px;background:var(--white);box-shadow:0 2px 14px rgba(0,0,0,.1);text-align:center}

/* footer */
.footer{left:0;top:3163px;width:1200px;height:502px;background:var(--brand)}
.footbar{left:0;top:3665px;width:1200px;height:47px;background:var(--brand-dark);color:#dde;font-size:10px;display:flex;align-items:center;justify-content:center}
.fh{font-family:"Ubuntu",sans-serif;font-size:15px;color:var(--white)}
.flist{list-style:none;font-size:10.5px;color:#e4e7ef;line-height:19.5px}
.flist li::before{content:"";display:inline-block;width:6px;height:6px;border:2px solid #e4e7ef;border-radius:50%;margin-right:9px;vertical-align:0}
.social{width:30px;height:30px;border-radius:50%;background:var(--brand-dark)}
</style>
</head>
<body>

<!-- Header -->
<svg class="abs" style="left:0;top:0" width="380" height="131" viewBox="0 0 380 131"><path d="M0 0H375L305 100Q283 131 245 131H0Z" fill="#4b5b84"/></svg>
<div class="abs brand-dot"></div>
<div class="abs brand-mark">LARKFORGE</div>
<nav class="abs nav"><span>Home</span><span>About Us</span><span>Products</span><span>Home Builts</span><span>Contact Us</span></nav>

<!-- Hero image -->
<svg class="abs" style="left:590px;top:0" width="610" height="720" viewBox="0 0 610 720">
  <defs>
    <linearGradient id="fire" x1="0" y1="0" x2="0.6" y2="1">
      <stop offset="0" stop-color="#59614f"/>
      <stop offset=".45" stop-color="#2a2522"/>
      <stop offset=".62" stop-color="#c9642a"/>
      <stop offset=".8" stop-color="#3a3430"/>
      <stop offset="1" stop-color="#8a8780"/>
    </linearGradient>
  </defs>
  <path d="M230 0 H610 V705 H160 Q130 705 115 680 L20 520 Q5 495 20 470 L115 300 L160 225 Q175 200 175 180 V90 Q175 60 200 40 Z" fill="#fff"/>
  <path d="M245 8 H610 V695 H170 Q145 695 132 672 L40 515 Q28 495 40 473 L130 315 L180 230 Q192 210 192 188 V95 Q192 68 212 50 Z" fill="url(#fire)" role="img" aria-label="Black steel outdoor fire pit burning logs on a stone patio"/>
</svg>
<div class="abs icon-hex hex" style="left:943px;top:35px;background:#fff"></div>
<div class="abs icon-hex hex" style="left:946px;top:38px;width:40px;height:44px;background:#2b2a28"></div>
<svg class="abs" style="left:956px;top:50px" width="20" height="20" viewBox="0 0 20 20" fill="none" stroke="#fff" stroke-width="1.8"><path d="M2 3h3l2 9h9l2-6H6"/><circle cx="8" cy="16" r="1.3"/><circle cx="15" cy="16" r="1.3"/></svg>
<div class="abs icon-hex hex" style="left:995px;top:35px;background:#fff"></div>
<div class="abs icon-hex hex" style="left:998px;top:38px;width:40px;height:44px;background:#2b2a28"></div>
<svg class="abs" style="left:1008px;top:50px" width="20" height="20" viewBox="0 0 20 20" fill="#fff"><circle cx="10" cy="6" r="3.5"/><path d="M3 18c0-5 3-7 7-7s7 2 7 7z"/></svg>
<div class="abs signup">Sign Up</div>
<div class="dots" style="left:875px;top:665px;width:70px;height:95px"></div>

<!-- Hero text -->
<div class="abs eyebrow" style="left:162px;top:268px">LARK FORGE</div>
<h1 class="abs h-title hero-title">Lark Forge<br>Outdoor Fire Pit</h1>
<p class="abs hero-copy">Lorem Ipsum is simply dummy text of the printing and typesetting industry.<br>Lorem Ipsum has been the industry's standard dummy text.</p>
<div class="btn" style="left:161px;top:525px;width:165px;height:52px;font-size:18px">Add To Cart</div>
<div class="hex-soft" style="left:-110px;top:555px;width:190px;height:235px"></div>

<!-- About -->
<div class="hex" style="left:190px;top:735px;width:375px;height:405px;background:#fff"></div>
<div class="hex" role="img" aria-label="White steel mailbox with gold emblem on a post beside a lawn" style="left:202px;top:747px;width:351px;height:381px;background:linear-gradient(135deg,#6f9a55,#e8eaea 45%,#c9cbc9 60%,#6f8f52)"></div>
<div class="hex" style="left:103px;top:1085px;width:190px;height:210px;background:#fff"></div>
<div class="hex" role="img" aria-label="White steel shelf brackets mounted on a brick wall" style="left:111px;top:1093px;width:174px;height:194px;background:linear-gradient(160deg,#c9b59b,#a78a6c 60%,#d8d2c8)"></div>
<div class="dots" style="left:165px;top:890px;width:40px;height:105px"></div>
<div class="abs eyebrow" style="left:612px;top:818px">LARK FORGE</div>
<h2 class="abs h-title" style="left:612px;top:835px;font-size:34px">About Lark Forge</h2>
<p class="abs copy" style="left:612px;top:904px;width:290px">Lorem Ipsum is simply dummy text of the printing and typesetting industry. Lorem Ipsum has been the industry's standard dummy text ever since the 1500s, when an unknown printer took a galley of type and scrambled it to make a type specimen book. It has survived not only five centuries, but also the leap into electronic typesetting, remaining essentially unchanged.</p>
<div class="btn" style="left:612px;top:1087px;width:134px;height:41px;font-size:14px">Explore More</div>
<div class="hex-soft" style="left:1115px;top:1095px;width:170px;height:190px"></div>

<!-- Products -->
<div class="abs eyebrow" style="left:0;width:1200px;text-align:center;top:1315px">LARK FORGE</div>
<h2 class="abs h-title" style="left:0;width:1200px;text-align:center;top:1336px;font-size:34px">Lark Forge Products</h2>
<p class="abs copy" style="left:380px;top:1385px;width:440px;text-align:center">Lorem Ipsum is simply dummy text of the printing and typesetting industry. Lorem Ipsum has been the industry's standard dummy text ever since the 1500s.</p>

<div class="abs photo-band" role="img" aria-label="Modern home exterior at dusk behind the product showcase"></div>

<div class="panel" style="left:161px;top:1630px;width:300px;height:475px"></div>
<div class="vlabel" style="left:183px;top:1690px;height:180px">LARK FORGE PRODUCTS</div>
<div class="card" style="left:229px;top:1668px;width:300px;height:225px">
  <div class="product-photo" role="img" aria-label="Copper steel cookery fire bowl with mesh lid" style="left:50px;top:22px;width:200px;height:130px;background:linear-gradient(180deg,#ece4de,#d8b9a2)"></div>
  <span class="abs" style="left:26px;top:185px">Steel Cookery</span>
  <span class="abs" style="left:163px;top:178px;font-size:22px;color:var(--brand)"><span style="font-size:16px;color:#111">$ </span>45.50</span>
</div>
<div class="abs" style="left:190px;top:1913px;color:#fff;font-size:14px;font-family:'Ubuntu',sans-serif">Steel Cookery</div>
<p class="abs" style="left:189px;top:1935px;width:260px;font-size:10.5px;line-height:19.5px;color:#e6e9f0">Lorem Ipsum is simply dummy text of the printing and typesetting industry. Lorem Ipsum has been the industry's standard dummy text ever since the 1500s.</p>
<div class="abs" style="left:188px;top:2031px;width:104px;height:40px;background:#fff;border-radius:4px;color:var(--brand);font-size:13px;display:flex;align-items:center;justify-content:center;font-weight:700">Buy Now</div>
<div class="ghost" style="left:307px;top:2031px;width:120px;height:40px">Add To Cart</div>

<div class="panel" style="left:574px;top:1480px;width:300px;height:300px"></div>
<div class="vlabel" style="left:596px;top:1540px;height:180px">LARK FORGE PRODUCTS</div>
<div class="card" style="left:641px;top:1516px;width:300px;height:226px">
  <div class="product-photo" role="img" aria-label="Pair of black steel wall brackets" style="left:50px;top:20px;width:200px;height:140px;background:linear-gradient(180deg,#e9eaec,#cfd1d5)"></div>
  <span class="abs" style="left:0;width:300px;top:187px">Steel Brackets</span>
</div>

<div class="panel" style="left:574px;top:1807px;width:300px;height:298px"></div>
<div class="vlabel" style="left:596px;top:1865px;height:180px">LARK FORGE PRODUCTS</div>
<div class="card" style="left:641px;top:1843px;width:300px;height:226px">
  <div class="product-photo" role="img" aria-label="Black steel mailbox with red flag" style="left:50px;top:20px;width:200px;height:140px;background:linear-gradient(180deg,#e6e6e8,#c9cacd)"></div>
  <span class="abs" style="left:0;width:300px;top:185px">Steel Mail Boxes</span>
</div>
<div class="dots" style="left:1045px;top:1710px;width:40px;height:100px"></div>

<!-- Customize -->
<div class="abs eyebrow" style="left:162px;top:2215px">LARK FORGE</div>
<h2 class="abs h-title" style="left:162px;top:2236px;font-size:34px">Customize Your Own</h2>
<p class="abs copy" style="left:162px;top:2306px;width:290px">Lorem Ipsum is simply dummy text of the printing and typesetting industry. Lorem Ipsum has been the industry's standard dummy text ever since the 1500s, when an unknown printer took a galley of type and scrambled it to make a type specimen book. It has survived not only five centuries, but also the leap into electronic typesetting, remaining essentially unchanged.</p>
<div class="btn" style="left:161px;top:2488px;width:150px;height:41px;font-size:14px">Customize Now</div>
<div class="hex-soft" style="left:-95px;top:2305px;width:155px;height:140px"></div>

<div class="hex" style="left:612px;top:2170px;width:190px;height:205px;background:#fff"></div>
<div class="hex" role="img" aria-label="Polished chrome wall bracket" style="left:620px;top:2178px;width:174px;height:189px;background:linear-gradient(135deg,#f2f3f8,#b9bdcc 50%,#e5e7ef)"></div>
<div class="hex" style="left:817px;top:2195px;width:222px;height:240px;background:#fff"></div>
<div class="hex" role="img" aria-label="Square steel fire table with flames in a garden" style="left:826px;top:2204px;width:204px;height:222px;background:linear-gradient(180deg,#6f8a3f,#c7762c 40%,#4b2e22 65%,#2e1f1a)"></div>
<div class="hex" style="left:672px;top:2375px;width:186px;height:200px;background:#fff"></div>
<div class="hex" role="img" aria-label="Ornate copper mailbox on a wrought iron gate" style="left:680px;top:2383px;width:170px;height:184px;background:linear-gradient(180deg,#2e3a2a,#6a4b35 55%,#3a2b22)"></div>
<div class="dots" style="left:1040px;top:2270px;width:40px;height:100px"></div>

<!-- Testimonials -->
<div class="abs eyebrow" style="left:0;width:1200px;text-align:center;top:2649px">LARK FORGE</div>
<h2 class="abs h-title" style="left:0;width:1200px;text-align:center;top:2670px;font-size:34px">Lark Forge Testimonials</h2>
<p class="abs copy" style="left:380px;top:2720px;width:440px;text-align:center">Lorem Ipsum is simply dummy text of the printing and typesetting industry. Lorem Ipsum has been the industry's standard dummy text ever since the 1500s.</p>
<div class="hex-soft" style="left:1150px;top:2790px;width:110px;height:125px"></div>

<div class="abs quote-card">
  <span class="abs" style="left:24px;top:18px;font-size:54px;color:#ddd;font-family:Georgia,serif">&ldquo;</span>
  <span class="abs" style="right:24px;bottom:2px;font-size:54px;color:#ddd;font-family:Georgia,serif">&rdquo;</span>
  <div style="margin-top:54px;font-size:14px;color:#111">Client Name</div>
  <div style="font-size:11px;color:var(--brand);margin-top:3px">lorem ipsum dummy</div>
  <p class="copy" style="width:400px;margin:12px auto 0;font-size:10.5px">Lorem Ipsum is simply dummy text of the printing and typesetting industry. Lorem Ipsum has been the industry's standard dummy text ever since the 1500s, when an unknown printer took a galley of type and scrambled it to make a type specimen book.</p>
</div>
<div class="hex" role="img" aria-label="Client portrait" style="left:571px;top:2800px;width:60px;height:66px;background:linear-gradient(180deg,#c8cdd8,#2f3d5e)"></div>
<div class="hex" style="left:552px;top:3080px;width:12px;height:13px;background:#888"></div>
<div class="hex" style="left:553px;top:3081px;width:10px;height:11px;background:#fff"></div>
<div class="hex" style="left:594px;top:3080px;width:12px;height:13px;background:var(--brand)"></div>
<div class="hex" style="left:635px;top:3080px;width:12px;height:13px;background:#888"></div>
<div class="hex" style="left:636px;top:3081px;width:10px;height:11px;background:#fff"></div>

<!-- Footer -->
<div class="abs footer"></div>
<div class="abs eyebrow" style="left:162px;top:3210px;color:#fff">LARK FORGE</div>
<h3 class="abs" style="left:162px;top:3226px;font-family:'Ubuntu',sans-serif;font-weight:400;font-size:26px;line-height:37px;color:#fff">Don't Miss Offer Or Opportunities<br>To Grab Our Products</h3>
<div class="abs" style="left:654px;top:3226px;width:225px;height:36px;border:1px solid #c7cddc;border-radius:3px;color:#fff;font-size:10.5px;padding:12px 0 0 18px">Enter Email:</div>
<div class="abs" style="left:895px;top:3226px;width:142px;height:36px;background:#fff;border-radius:3px;color:var(--brand);font-size:14px;font-weight:700;display:flex;align-items:center;justify-content:center">Subscribe Now!</div>
<div class="abs" style="left:161px;top:3338px;width:877px;height:1px;background:#6e7c9f"></div>
<div class="abs" style="left:85px;top:3240px;width:20px;height:20px;border-radius:50%;background:#58688f"></div>
<div class="abs" style="left:1137px;top:3240px;width:26px;height:26px;border-radius:50%;border:1px solid #6a799c"></div>

<div class="abs" style="left:206px;top:3375px;width:18px;height:18px;border-radius:50%;border:2px solid #fff"></div>
<div class="abs" style="left:161px;top:3402px;color:#fff;font-weight:700;font-size:19px;letter-spacing:1px">LARKFORGE</div>
<p class="abs" style="left:162px;top:3445px;width:200px;font-size:10.5px;line-height:19.5px;color:#e4e7ef">Lorem Ipsum is simply dummy text of the printing and typesetting industry. Lorem Ipsum has been the industry's standard dummy text ever since the 1500s, when an unknown printer took a galley of type.</p>

<div class="abs fh" style="left:388px;top:3400px">Quick Links</div>
<ul class="abs flist" style="left:386px;top:3444px"><li>Home</li><li>About Us</li><li>Products</li><li>Home Built</li><li>Contact Us</li></ul>
<div class="abs fh" style="left:613px;top:3400px">Resources</div>
<ul class="abs flist" style="left:611px;top:3444px"><li>Offers</li><li>Terms &amp; Conditions</li><li>Privacy Policy</li><li>Testimonials</li><li>Newsletter</li></ul>
<div class="abs fh" style="left:838px;top:3400px">Contact Info</div>
<svg class="abs" style="left:838px;top:3442px" width="26" height="26" viewBox="0 0 26 26"><circle cx="13" cy="13" r="13" fill="#3e4b6e"/><path d="M9 8l2 0 1 3-1.5 1a7 7 0 0 0 3.5 3.5l1-1.5 3 1v2c-5 1-10-4-9-9z" fill="#fff"/></svg>
<div class="abs" style="left:875px;top:3450px;font-size:10.5px;color:#e4e7ef">+91-000-000-0000</div>
<svg class="abs" style="left:838px;top:3492px" width="26" height="26" viewBox="0 0 26 26"><circle cx="13" cy="13" r="13" fill="#3e4b6e"/><rect x="7.5" y="9" width="11" height="8" fill="none" stroke="#fff" stroke-width="1.3"/><path d="M7.5 9l5.5 4.5 5.5-4.5" fill="none" stroke="#fff" stroke-width="1.3"/></svg>
<div class="abs" style="left:875px;top:3499px;font-size:10.5px;color:#e4e7ef">info@larkforge.com</div>
<svg class="abs" style="left:838px;top:3543px" width="26" height="26" viewBox="0 0 26 26"><circle cx="13" cy="13" r="13" fill="#3e4b6e"/><path d="M13 20s-5-5-5-8.5a5 5 0 0 1 10 0C18 15 13 20 13 20z" fill="none" stroke="#fff" stroke-width="1.3"/><circle cx="13" cy="11.5" r="1.6" fill="#fff"/></svg>
<div class="abs" style="left:875px;top:3540px;width:140px;font-size:10.5px;line-height:19px;color:#e4e7ef">100 lorem ipsum is simply dummy text.</div>

<div class="abs social" style="left:518px;top:3588px"></div>
<div class="abs social" style="left:563px;top:3588px"></div>
<div class="abs social" style="left:607px;top:3588px"></div>
<div class="abs social" style="left:652px;top:3588px"></div>
<div class="hex" style="left:-40px;top:3560px;width:70px;height:80px;background:#58688f"></div>

<div class="abs footbar">Copyright © 2020 Lark Forge. All Rights Reserved.</div>

</body>
</html>
```